Tinker's Lamp sports bar beer & food menu

We need a menu design for our gastropub sports bar in L.A.'s Sawtelle Neighborhood (Little Osaka). We have a full-bar (hard liquor, craft beer, wine and cocktails) . We have a lunch and dinner menu as well as a happy hour menu. On Sundays we have a seperate menu with brunch items. The design concept is a British pub type of sports bar. We're looking for something different from our existing menu design. Ideally something cleaner and more legible. It should mesh a simple, modern sensibility with the more traditional darkened pub style of our interior design.

You can check out our Voxly page for photos of the interior/exterior:
https://www.reviewhatch.example/biz_photos/tinkers-lamp-los-angeles?tab=interior

You can view our existing menu here:
https://www.reviewhatch.example/biz_photos/tinkers-lamp-los-angeles?tab=menu

If there's an area of the design that can be a little more playful it's our highlighted event schedule so that the events will stand out.

Target Market(s)

Age of 25 and up. Sawtelle is a cultural hub that caters to a younger, moderately affluent crowd.

Industry/Entity Type

Sports Bar

Font styles to use
Sans Serif

Colors

Designer to choose colors to be used in the design.

Requirements
Must have
• Logo, highlighted event schedule (beer pong Monday, trivia Tuesday, taco Tuesday, whiskey Wednesday, karaoke Saturday). The menu should be easy to read in a darkened bar. We'll be printing on standard 8.5x11 in portrait.
Nice to have
• We're trying to have the menu take up as few pages as possible.
Should not have
• We're trying to have the menu take up as few pages as possible. Food photography isn't necessary. A cover isn't necessary. Please avoid clip art of food.

```html
<!DOCTYPE html>
<html lang="en">
<head>
<meta charset="utf-8">
<title>Tinker's Lamp — Pub &amp; Restaurant Menu</title>
<link href="https://fonts.googleapis.com/css2?family=Saira:ital,wght@0,500;0,600;0,700;1,400&display=swap" rel="stylesheet">
<style>
  :root {
    --backdrop: #cfcdce;
    --paper: #f3eeda;
    --frame: #d9c7ab;
    --frame-corner: #cfa88e;
    --accent: #f9ae3a;
    --ink: #262626;
    --ink-soft: #3a3a3a;
    --rule: #5a5a5a;
  }
  * { box-sizing: border-box; margin: 0; padding: 0; }
  html, body { width: 1200px; height: 1015px; overflow: hidden; background: var(--backdrop); }
  body { position: relative; font-family: "Saira", "Arial Narrow", sans-serif; color: var(--ink); }

  .page {
    position: absolute; top: 111px; width: 563px; height: 794px;
    background: var(--paper);
    box-shadow: 3px 4px 8px rgba(0,0,0,0.28);
  }
  .page--left { left: 33px; }
  .page--right { left: 612px; }

  .page-frame {
    position: absolute; inset: 10px; border: 7px solid var(--frame);
  }
  .page-frame__corner {
    position: absolute; width: 11px; height: 11px; background: var(--frame-corner);
  }
  .page-frame__corner--tl { top: -9px; left: -9px; }
  .page-frame__corner--tr { top: -9px; right: -9px; }
  .page-frame__corner--bl { bottom: -9px; left: -9px; }
  .page-frame__corner--br { bottom: -9px; right: -9px; }

  .brand {
    position: absolute; top: 34px; display: flex; align-items: center; gap: 8px;
  }
  .brand__mark { width: 26px; height: 26px; background: var(--accent); }
  .brand__name { font-weight: 700; font-size: 28px; line-height: 1; color: var(--ink); letter-spacing: 0.2px; }
  .brand__tag { position: absolute; left: 34px; top: 34px; font-size: 7px; letter-spacing: 3px; font-weight: 500; color: var(--ink); text-transform: uppercase; }

  .events {
    position: absolute; left: 373px; top: 30px; width: 152px; height: 79px;
    padding: 4px; background: var(--paper); border: 3px solid var(--frame);
  }
  .events__list {
    list-style: none; height: 100%; background: var(--accent);
    padding: 6px 18px 0 0; text-align: right;
    font-size: 10px; font-weight: 700; line-height: 11.4px; letter-spacing: 0.3px; color: var(--ink);
  }

  .section { position: absolute; left: 37px; right: 37px; }
  .section__title {
    width: 181px; height: 18px; padding-left: 6px;
    background: var(--accent); color: var(--ink-soft);
    font-size: 12px; font-weight: 700; line-height: 18px; text-transform: uppercase; letter-spacing: 0.2px;
  }
  .section--right-col .section__title { width: 181px; }

  .menu { list-style: none; margin-top: 9px; padding: 0 37px 0 16px; }
  .menu__item {
    display: grid; grid-template-columns: 1fr auto; column-gap: 12px;
    margin-bottom: var(--gap, 6px);
  }
  .menu__name { font-size: 11px; font-weight: 600; line-height: 13px; letter-spacing: 0.2px; }
  .menu__price { font-size: 11.5px; font-weight: 600; line-height: 13px; }
  .menu__desc {
    grid-column: 1 / 2; max-width: 270px; padding-left: 8px;
    font-size: 7.4px; font-style: italic; font-weight: 400; line-height: 9px; color: var(--ink-soft);
  }

  .divider { position: absolute; left: 38px; right: 38px; height: 0; display: flex; justify-content: space-between; }
  .divider span { width: 233px; border-top: 1.5px dotted var(--rule); }
  .page--right .divider span { width: 236px; }
</style>
</head>
<body>

<section class="page page--left" aria-label="Menu page one">
  <div class="page-frame" role="img" aria-label="Decorative scroll border framing the page">
    <span class="page-frame__corner page-frame__corner--tl"></span>
    <span class="page-frame__corner page-frame__corner--tr"></span>
    <span class="page-frame__corner page-frame__corner--bl"></span>
    <span class="page-frame__corner page-frame__corner--br"></span>
  </div>

  <header class="brand" style="left:44px">
    <span class="brand__mark"></span>
    <span class="brand__name">Tinker's Lamp</span>
    <span class="brand__tag">Pub &amp; Restaurant</span>
  </header>

  <aside class="events" aria-label="Weekly events">
    <ul class="events__list">
      <li>Beer Pong Monday</li>
      <li>Trivia Tuesday</li>
      <li>Taco Tuesday</li>
      <li>Whiskey Wednesday</li>
      <li>Karaoke Saturday</li>
    </ul>
  </aside>

  <div class="section" style="top:110px; --gap:5px">
    <h2 class="section__title">Burgers and Sandwiches</h2>
    <ul class="menu">
      <li class="menu__item"><span class="menu__name">Chicken Sandwich</span><span class="menu__price">$12</span><span class="menu__desc">Chicken Breast, Applewood Bacon, Butter Lettuce, White Cheddar, Avocado and Tomato Served on Sourdough Bread</span></li>
      <li class="menu__item"><span class="menu__name">Buttermilk Fried Chicken</span><span class="menu__price">$13</span><span class="menu__desc">Coleslaw, Provolone, Tomato, and a Spiced Mayonnaise on a Pretzel Roll</span></li>
      <li class="menu__item"><span class="menu__name">Short Rib Sandwich</span><span class="menu__price">$13</span><span class="menu__desc">Beef Shorts, Mayo, Tomato, Caramelized Onions, Arugula, Pepper Jack Cheese Served on Sourdough Bread</span></li>
      <li class="menu__item"><span class="menu__name">Grilled Cheese Sandwich</span><span class="menu__price">$13</span><span class="menu__desc">Cheese, Provolone and Cheddar Cheese</span></li>
      <li class="menu__item"><span class="menu__name">Tinker's Lamp Burger</span><span class="menu__price">$14</span><span class="menu__desc">Sharp Cheddar, Arugula, Roasted Shallots, Bacon Jam with Malt Aioli</span></li>
      <li class="menu__item"><span class="menu__name">The Truffle Burger</span><span class="menu__price">$15</span><span class="menu__desc">Caramelized Onions, Arugula, Truffle Pecorino, Truffle Mayo and Truffle Fries</span></li>
      <li class="menu__item"><span class="menu__name">The Sloppy Joe</span><span class="menu__price">$10</span><span class="menu__desc">Shredded Lettuce and Sharp Cheddar</span></li>
      <li class="menu__item"><span class="menu__name">Veggie Burger</span><span class="menu__price">$12</span><span class="menu__desc">Concoction of kale, Tomato, Avocado, Sharp Cheddar with a Balsamic Reduction</span></li>
      <li class="menu__item"><span class="menu__name">Flat Iron Steak Sandwich</span><span class="menu__price">$16</span><span class="menu__desc">Arugula, Peppers, Fontina, Onion and Mayo</span></li>
      <li class="menu__item"><span class="menu__name">Chicken Spinach Wrap</span><span class="menu__price">$10</span><span class="menu__desc">Chicken, Bacon, Lettuce, Tomato, Avocado, Ranch and Mayo</span></li>
      <li class="menu__item"><span class="menu__name">Fried Chicken Sliders (4)</span><span class="menu__price">$12</span><span class="menu__desc">Coleslaw, Lime Sriracha Sauce</span></li>
    </ul>
  </div>

  <div class="divider" style="top:489px"><span></span><span></span></div>

  <div class="section" style="top:505px; --gap:6px">
    <h2 class="section__title">Big Dog Bites</h2>
    <ul class="menu">
      <li class="menu__item"><span class="menu__name">Atlantic Cod Fish N' Chips</span><span class="menu__price">$15</span><span class="menu__desc">House Tartar Sauce, Vinegar and Lemon Wedge</span></li>
      <li class="menu__item"><span class="menu__name">Oven Roasted ½ Roasted Chicken</span><span class="menu__price">$16</span><span class="menu__desc">Boneless Chicken, Broccolini, Fingerling Potatoes, Topped with Chimichurri Sauce</span></li>
      <li class="menu__item"><span class="menu__name">Black Mussels</span><span class="menu__price">$17</span><span class="menu__desc">Tequila Chipotle Sauce, Cilantro and Cherry Tomatoes</span></li>
      <li class="menu__item"><span class="menu__name">Flat Iron Steak</span><span class="menu__price">$19</span><span class="menu__desc">French Fries, Baby Arugula in a Light peppercorn Sauce</span></li>
    </ul>
  </div>

  <div class="divider" style="top:669px"><span></span><span></span></div>

  <div class="section" style="top:686px; --gap:5px">
    <h2 class="section__title">Flatbreads</h2>
    <ul class="menu" style="margin-top:5px">
      <li class="menu__item"><span class="menu__name">Margherita</span><span class="menu__price">$12</span><span class="menu__desc">Fresh Mozzarella, Roma Tomatoes and Fresh Italian Basil</span></li>
      <li class="menu__item"><span class="menu__name">Vegetarian</span><span class="menu__price">$13</span><span class="menu__desc">Brussel Sprouts, Peppers, Onions, Zucchini, Goat Cheese, Smoked Mozzarella Topped with a Balsamic Reduction</span></li>
    </ul>
  </div>
</section>

<section class="page page--right" aria-label="Menu page two">
  <div class="page-frame" role="img" aria-label="Decorative scroll border framing the page">
    <span class="page-frame__corner page-frame__corner--tl"></span>
    <span class="page-frame__corner page-frame__corner--tr"></span>
    <span class="page-frame__corner page-frame__corner--bl"></span>
    <span class="page-frame__corner page-frame__corner--br"></span>
  </div>

  <header class="brand" style="left:44px">
    <span class="brand__mark"></span>
    <span class="brand__name">Tinker's Lamp</span>
    <span class="brand__tag">Pub &amp; Restaurant</span>
  </header>

  <div class="section" style="top:98px; --gap:10px">
    <ul class="menu">
      <li class="menu__item"><span class="menu__name">Prosciutto &amp; Arugula</span><span class="menu__price">$14</span><span class="menu__desc">Red Onion, Parmesan, Mozzarella</span></li>
      <li class="menu__item"><span class="menu__name">Portobello &amp; Truffle</span><span class="menu__price">$14</span><span class="menu__desc">Portobello White Mushroom, Fontina, Drizzled with Truffle Oil</span></li>
      <li class="menu__item"><span class="menu__name">Chicken Tikka Masala</span><span class="menu__price">$14</span><span class="menu__desc">Tandoori Chicken, Fontini and Raita</span></li>
      <li class="menu__item"><span class="menu__name">The Tinker's Lamp</span><span class="menu__price">$15</span><span class="menu__desc">Meatballs, Sausage, Chorizo, Mozzarella and Fresen</span></li>
    </ul>
  </div>

  <div class="divider" style="top:236px"><span></span><span></span></div>

  <div class="section" style="top:253px; --gap:7px">
    <h2 class="section__title">For the Table</h2>
    <ul class="menu" style="margin-top:8px">
      <li class="menu__item"><span class="menu__name">Tinker's 3 Whole Wings</span><span class="menu__price">$9</span><span class="menu__desc">Choice of Dry Rub, Sweet N' Spicy or Buffalo</span></li>
      <li class="menu__item"><span class="menu__name">Brussel Sprouts</span><span class="menu__price">$8</span><span class="menu__desc">Sautéed with Chorizo, Roasted Almonds and Golden Raisins</span></li>
      <li class="menu__item"><span class="menu__name">Golden Calamari</span><span class="menu__price">$11</span><span class="menu__desc">Traditionally Served with Spiced Marinara</span></li>
      <li class="menu__item"><span class="menu__name">Shrimp Mac N' Cheese</span><span class="menu__price">$12</span><span class="menu__desc">Baked with Fontina, Sharp Cheddar and Parmesan</span></li>
      <li class="menu__item"><span class="menu__name">S½ Dozen Oysters</span><span class="menu__price">$12</span><span class="menu__desc">Cove Point's Served with Our Own Mignonette</span></li>
      <li class="menu__item"><span class="menu__name">Charcuterie</span><span class="menu__price">$15</span><span class="menu__desc">Seasonal Meats and Cheese</span></li>
      <li class="menu__item"><span class="menu__name">Nachos</span><span class="menu__price">$9</span><span class="menu__desc" style="max-width:320px">Medley of Black Beans, Pico De Gallo, Cheese, Jalapeno and Sour Cream</span></li>
      <li class="menu__item"><span class="menu__name">Mozzarella Cheese Ctick</span><span class="menu__price">$9</span></li>
    </ul>
  </div>

  <div class="divider" style="top:512px"><span></span><span></span></div>

  <div class="section" style="top:529px; --gap:4px">
    <h2 class="section__title">Sides</h2>
    <ul class="menu" style="margin-top:7px">
      <li class="menu__item"><span class="menu__name">House Fries</span><span class="menu__price">$6</span></li>
      <li class="menu__item"><span class="menu__name">Truffle Fries</span><span class="menu__price">$7</span></li>
      <li class="menu__item"><span class="menu__name">Dry Rub Fries</span><span class="menu__price">$6</span></li>
      <li class="menu__item"><span class="menu__name">Sweet Potato Fries</span><span class="menu__price">$7</span></li>
    </ul>
  </div>

  <div class="divider" style="top:630px"><span></span><span></span></div>

  <div class="section" style="top:646px; --gap:4px">
    <h2 class="section__title">Dessert</h2>
    <ul class="menu" style="margin-top:7px">
      <li class="menu__item"><span class="menu__name">Coco Flan</span><span class="menu__price">$9</span></li>
      <li class="menu__item"><span class="menu__name">Cheese Cake</span><span class="menu__price">$9</span></li>
      <li class="menu__item"><span class="menu__name">Peach Tart</span><span class="menu__price">$9</span></li>
    </ul>
  </div>
</section>

</body>
</html>
```